Structural Engineering Business Card

Brookvane Drafting does residential house plans for clients in Central Florida. Would like simple but elegant business card that is appropriate for a house plan engineering company. Prefer black business card with black/white them but open to other shades of blue. I uploaded a sample card that I came across that looked good but please come up with your own creative designs.

Contact Information for Business Card

Name, Title, Phone, Email, Address, website

```html
<!DOCTYPE html>
<html lang="en">
<head>
<meta charset="utf-8">
<title>Brookvane Drafting — Business Card</title>
<link href="https://fonts.googleapis.com/css2?family=Montserrat:wght@400;600;800&family=Arimo:wght@400&display=swap" rel="stylesheet">
<style>
  :root {
    --backdrop: #2a2a2a;
    --card-dark: #000000;
    --card-light: #ffffff;
    --ink-light: #ffffff;
    --ink-dark: #111111;
    --ink-muted: #333333;
  }
  * { box-sizing: border-box; margin: 0; padding: 0; }
  html, body {
    width: 1200px;
    height: 1015px;
    overflow: hidden;
    background: var(--backdrop);
  }
  .sheet {
    width: 1200px;
    height: 1015px;
    display: flex;
    flex-direction: column;
    align-items: center;
    justify-content: center;
    gap: 40px;
  }
  .card {
    width: 760px;
    height: 434px;
    display: flex;
    flex-direction: column;
    align-items: center;
    justify-content: center;
    box-shadow: 0 10px 30px rgba(0,0,0,0.45);
  }
  .card--front { background: var(--card-dark); }
  .card--back { background: var(--card-light); }

  .wordmark {
    display: flex;
    align-items: center;
    gap: 16px;
    font-family: "Montserrat", sans-serif;
    font-weight: 800;
    text-transform: uppercase;
    letter-spacing: 0.5px;
  }
  .wordmark__square {
    width: 0.8em;
    height: 0.8em;
    background: currentColor;
  }
  .card--front .wordmark {
    color: var(--ink-light);
    font-size: 52px;
  }
  .card--back .wordmark {
    color: var(--ink-dark);
    font-size: 30px;
    gap: 10px;
    margin-bottom: 26px;
  }

  .holder {
    text-align: center;
    margin-bottom: 18px;
  }
  .holder__name {
    font-family: "Montserrat", sans-serif;
    font-weight: 600;
    font-size: 24px;
    letter-spacing: 1px;
    text-transform: uppercase;
    color: var(--ink-dark);
  }
  .holder__title {
    font-family: "Arimo", sans-serif;
    font-size: 15px;
    letter-spacing: 1.5px;
    text-transform: uppercase;
    color: var(--ink-muted);
  }
  .contact {
    font-family: "Arimo", sans-serif;
    font-size: 19px;
    line-height: 1.3;
    color: var(--ink-dark);
    text-align: center;
    list-style: none;
  }
  .contact--address { margin-top: 12px; }
</style>
</head>
<body>
  <main class="sheet">
    <section class="card card--front" aria-label="Card front">
      <div class="wordmark"><span class="wordmark__square"></span><span>Brookvane Drafting</span></div>
    </section>

    <section class="card card--back" aria-label="Card back">
      <div class="wordmark"><span class="wordmark__square"></span><span>Brookvane Drafting</span></div>
      <div class="holder">
        <p class="holder__name">Daniel Harlow</p>
        <p class="holder__title">Managing Director</p>
      </div>
      <ul class="contact">
        <li>044-987 654 321</li>
        <li>hello@brookvanedrafting.com</li>
        <li>www.brookvanedrafting.com</li>
      </ul>
      <ul class="contact contact--address">
        <li>218, Cypress Hollow Road</li>
        <li>32801, United States</li>
      </ul>
    </section>
  </main>
</body>
</html>
```